Web design for Crowdfunding site HopeWingsRally.com

We need a web design for christian crowdfunding website. Here is the challenge: We need responsive layout that is targeted first in iPad size of screen. It should also scale somehow down to iPhone size of screens. Web layout can be about the same size as iPad screen.

Screens should work so that main page scrolls not but only certain part of the screen scrolls and always one "page" at time. We can implement these "scrolls" then later with javascript but now we need only design. The challenge is to create this kind of hybrid website / app look.

Target is at first to raise funds to orphan people needing about $40 per month for their living and education. There is always some organization which takes care of these kids. Later there will be other christian missions included. At first we are looking to find monthly supporters.

You can be as creative as you want :) As you see from the look and feel sector, I am not looking any same traditional look which many "help kids" sites have. I am looking to reach now younger generation and therefore iPad and mobile are the main screen sizes.

Inspirational designs:
- https://example-gallery.test/profiles/studiofernlake/designs/482716?from=%2Fbrowse%2Fxhr%2Fdesigns%3Fcategory%3Dmobile-app-design
- http://www.artpoolhub.test/design/8261047 Clear, simple visuals
- http://www.artpoolhub.test/design/7394215 Header
- http://www.artpoolhub.test/design/6048392 Contrast in the colors, i think is powerfull

Some terms could be: Kids play, kids are learning (in the school). No static posture but living like kids are. I wonder also how we could also add little bit gaming style even though the question is of reali life of real people. Giving should be rewarding.

Target Market(s)

People who want help other people.

Industry/Entity Type

Christian

Number of Pages Required

4 page

Requirements
Must have
• Homepage. Mission page (In my wireframes it was one kid).
Nice to have
• Other pages and some idea how to scroll. 4 pages is no must. If you feel easy, please give first some draft and I give comments on that.

```html
<!DOCTYPE html>
<html lang="en">
<head>
<meta charset="utf-8">
<title>HopeWingsRally – Mission: Orphan Elina, 11y</title>
<link href="https://fonts.googleapis.com/css2?family=Roboto+Slab:wght@300;400;700&family=Roboto:wght@400&display=swap" rel="stylesheet">
<style>
:root{
  --orange:#ffad00;
  --teal:#1cc0c8;
  --ink:#555555;
  --ink-soft:#6a6a6a;
  --header-bg:#f5f5f5;
  --card-bg:#ffffff;
  --rail:#d4d4d4;
  --line:#d9d9d9;
}
*{margin:0;padding:0;box-sizing:border-box}
html,body{width:1200px;height:860px;overflow:hidden}
body{background:var(--orange);font-family:'Roboto Slab',serif;color:var(--ink);position:relative}
.page-card{position:absolute;left:99px;top:63px;width:1005px;height:700px;background:var(--card-bg)}
.site-header{position:absolute;left:0;top:0;width:100%;height:81px;background:var(--header-bg)}
.missions-link{position:absolute;left:48px;top:22px;display:flex;align-items:center;gap:8px;font-size:13px;color:var(--ink)}
.missions-link svg{display:block}
.site-logo{position:absolute;left:0;width:100%;top:20px;text-align:center;font-size:22px;font-weight:700;color:var(--ink);letter-spacing:.2px}
.account-links{position:absolute;right:46px;top:22px;display:flex;align-items:center;gap:24px;font-size:13px}
.account-links span{display:flex;align-items:center;gap:7px}
.social-links{position:absolute;right:46px;top:51px;display:flex;gap:14px}
.social-links i{display:block;width:11px;height:11px;border-radius:2px;background:var(--ink)}
.mission-main{position:absolute;left:68px;top:0;width:550px}
.mission-title{position:absolute;top:96px;font-size:17px;font-weight:700;white-space:nowrap}
.tabs{position:absolute;top:139px;left:0;width:550px;height:38px;display:flex;background:var(--orange);font-size:13px}
.tab{display:flex;align-items:center;justify-content:center;color:var(--ink)}
.tab-story{width:167px;background:#fff;border:1px solid #ddd}
.tab-updates{width:185px}
.tab-comments{flex:1}
.timeline{position:absolute;left:-23px;top:200px;width:6px;height:437px;background:var(--rail);border-radius:3px}
.timeline-dot{position:absolute;left:-6.5px;width:19px;height:19px;border-radius:50%;background:var(--rail)}
.timeline-dot.is-current{background:var(--orange)}
.story-text{position:absolute;left:0;width:550px;font-size:11.3px;line-height:18.9px;color:var(--ink-soft);text-align:justify;font-weight:400}
.story-photo{position:absolute;left:0;top:316px;width:550px;height:186px;background:linear-gradient(100deg,#e9d9b8 0%,#a9622c 30%,#c47a3a 55%,#8a4a22 75%,#2fa8d4 100%)}
.mission-aside{position:absolute;left:655px;top:0;width:303px}
.child-name{position:absolute;top:96px;font-size:17px;font-weight:700;white-space:nowrap}
.child-meta{position:absolute;top:133px;font-size:12.5px;line-height:21px;color:var(--ink-soft)}
.child-meta .location{display:flex;align-items:center;gap:7px}
.support-bar{position:absolute;top:203px;left:0;width:303px;height:36px;background:var(--orange);display:flex;align-items:center;padding:0 12px;color:#fff;font-size:13px;font-weight:300}
.support-bar .supporters{display:flex;gap:27px;margin-left:14px}
.support-bar .chevron{margin-left:auto}
.support-level{position:absolute;top:255px;font-size:15px;font-weight:700;white-space:nowrap}
.progress-ring{position:absolute;left:0;top:296px}
.progress-ring text{font-family:'Roboto Slab',serif;font-size:17px;font-weight:700;fill:#aaa}
.funding-facts{position:absolute;left:117px;top:308px;font-size:14px;line-height:24.5px;color:var(--ink-soft)}
.funding-facts .given{font-size:15px;font-weight:700;color:var(--ink-soft)}
.funding-facts .per-month{display:flex;align-items:center;gap:8px}
.participate-head{position:absolute;top:419px;left:0;width:303px;height:36px;background:var(--orange);color:#fff;font-size:14px;display:flex;align-items:center;padding-left:13px;font-weight:400}
.pledge-list{position:absolute;top:455px;left:0;width:303px;list-style:none}
.pledge{height:43px;display:flex;align-items:center;font-size:13px;border-bottom:1px solid var(--line);color:var(--ink)}
.pledge:last-child{border-bottom:none}
.pledge .person{margin-right:11px}
.pledge .cart{margin-left:auto;margin-right:17px}
.pledge .amount-input{margin-left:32px;font-size:12px;font-style:italic;font-family:'Roboto',sans-serif;color:#aaa;font-weight:400}
.site-footer{position:absolute;left:0;width:100%;top:801px;text-align:center;font-family:'Roboto',sans-serif;font-size:13.5px;color:#fff}
</style>
</head>
<body>
<div class="page-card">
  <header class="site-header">
    <div class="missions-link">
      <svg width="13" height="11" viewBox="0 0 13 11"><g fill="#555"><rect x="0" y="0" width="2" height="2"/><rect x="3" y="0" width="10" height="2"/><rect x="0" y="3" width="2" height="2"/><rect x="3" y="3" width="10" height="2"/><rect x="0" y="6" width="2" height="2"/><rect x="3" y="6" width="10" height="2"/><rect x="0" y="9" width="2" height="2"/><rect x="3" y="9" width="10" height="2"/></g></svg>
      <span>SEE THE MISSIONS</span>
      <svg width="13" height="13" viewBox="0 0 13 13" style="margin-left:6px"><circle cx="5.5" cy="5.5" r="4" fill="none" stroke="#555" stroke-width="2"/><line x1="8.5" y1="8.5" x2="12" y2="12" stroke="#555" stroke-width="2.2" stroke-linecap="round"/></svg>
    </div>
    <div class="site-logo">HOPEWINGSRALLY</div>
    <nav class="account-links">
      <span><svg width="10" height="11" viewBox="0 0 10 11"><circle cx="5" cy="3" r="2.8" fill="#555"/><path d="M0 11c0-3.5 2-5 5-5s5 1.5 5 5z" fill="#555"/></svg>LOG IN</span>
      <span>SIGN UP</span>
    </nav>
    <div class="social-links"><i></i><i></i><i></i><i></i></div>
  </header>

  <main class="mission-main">
    <h1 class="mission-title">Mission: Orphan Elina, 11y</h1>
    <div class="tabs">
      <div class="tab tab-story">Story</div>
      <div class="tab tab-updates">Updates</div>
      <div class="tab tab-comments">Comments</div>
    </div>
    <div class="timeline">
      <span class="timeline-dot" style="top:-5px"></span>
      <span class="timeline-dot is-current" style="top:215px"></span>
      <span class="timeline-dot" style="top:423px"></span>
    </div>
    <p class="story-text" style="top:198px">There are many variations of passages of Lorem Ipsum available, but the majority have suffered alteration in some form, by injected humour, or randomised words which don't look even slightly believable. If you are going to use a passage of Lorem Ipsum, you need to be sure there isn't anything embarrassing hidden in the middle of text. All the Lorem Ipsum generators on the Internet tend to repeat predefined chunks as necessary, making this the first true generator on the Internet.</p>
    <div class="story-photo" role="img" aria-label="Photo of a wooden desk with a keyboard, papers and a hand on a mouse"></div>
    <p class="story-text" style="top:518px">There are many variations of passages of Lorem Ipsum available, but the majority have suffered alteration in some form, by injected humour, or randomised words which don't look even slightly believable. If you are going to use a passage of Lorem Ipsum, you need to be sure there isn't anything embarrassing hidden in the middle of text.</p>
    <p class="story-text" style="top:612px">All the Lorem Ipsum generators on the Internet tend to repeat predefined chunks as necessary, making this the first true generator on the Internet. voluptatem accusantium doloremque laudantium, totam rem aperiam, eaque ipsa quae ab illo inventore veritatis et quasi architecto.</p>
  </main>

  <aside class="mission-aside">
    <h2 class="child-name">Name : Elina, 11y</h2>
    <div class="child-meta">
      <div class="location"><svg width="10" height="14" viewBox="0 0 10 14"><path d="M5 0a5 5 0 0 0-5 5c0 3.5 5 9 5 9s5-5.5 5-9a5 5 0 0 0-5-5z" fill="#666"/><circle cx="5" cy="5" r="1.8" fill="#fff"/></svg>Rivenpur</div>
      <div>Organization:&nbsp; Ashford Care</div>
    </div>
    <div class="support-bar">
      <span>Support:</span>
      <span class="supporters">
        <svg width="14" height="15" viewBox="0 0 10 11"><circle cx="5" cy="3" r="2.8" fill="#fff"/><path d="M0 11c0-3.5 2-5 5-5s5 1.5 5 5z" fill="#fff"/></svg>
        <svg width="14" height="15" viewBox="0 0 10 11"><circle cx="5" cy="3" r="2.8" fill="#fff"/><path d="M0 11c0-3.5 2-5 5-5s5 1.5 5 5z" fill="#fff"/></svg>
        <svg width="14" height="15" viewBox="0 0 10 11"><circle cx="5" cy="3" r="2.8" fill="#fff"/><path d="M0 11c0-3.5 2-5 5-5s5 1.5 5 5z" fill="#fff"/></svg>
        <svg width="14" height="15" viewBox="0 0 10 11"><circle cx="5" cy="3" r="2.8" fill="#fff"/><path d="M0 11c0-3.5 2-5 5-5s5 1.5 5 5z" fill="#fff"/></svg>
        <svg width="14" height="15" viewBox="0 0 10 11"><circle cx="5" cy="3" r="2.8" fill="#fff"/><path d="M0 11c0-3.5 2-5 5-5s5 1.5 5 5z" fill="#fff"/></svg>
      </span>
      <svg class="chevron" width="7" height="11" viewBox="0 0 7 11"><path d="M1 1l4.5 4.5L1 10" fill="none" stroke="#fff" stroke-width="1.6"/></svg>
    </div>
    <h3 class="support-level">My Support is Now: $5 / Month</h3>
    <svg class="progress-ring" width="96" height="96" viewBox="0 0 96 96">
      <circle cx="48" cy="48" r="42" fill="none" stroke="#d0d0d0" stroke-width="7"/>
      <circle cx="48" cy="48" r="42" fill="none" stroke="var(--teal)" stroke-width="8" pathLength="100" stroke-dasharray="39 61" transform="rotate(-80 48 48)"/>
      <text x="48" y="54" text-anchor="middle">45 %</text>
    </svg>
    <div class="funding-facts">
      <div class="given">$15 Given</div>
      <div>of total $35 needed</div>
      <div class="per-month"><svg width="14" height="14" viewBox="0 0 14 14"><rect x="1" y="2.5" width="12" height="10.5" fill="none" stroke="#777" stroke-width="1.2"/><line x1="1" y1="5.5" x2="13" y2="5.5" stroke="#777" stroke-width="1.2"/><line x1="4" y1="0.5" x2="4" y2="3.5" stroke="#777" stroke-width="1.4"/><line x1="10" y1="0.5" x2="10" y2="3.5" stroke="#777" stroke-width="1.4"/><g fill="#777"><rect x="3" y="7.5" width="2" height="1.5"/><rect x="6" y="7.5" width="2" height="1.5"/><rect x="9" y="7.5" width="2" height="1.5"/><rect x="3" y="10" width="2" height="1.5"/><rect x="6" y="10" width="2" height="1.5"/><rect x="9" y="10" width="2" height="1.5"/></g></svg>Per Month need</div>
    </div>
    <div class="participate-head">Participate</div>
    <ul class="pledge-list">
      <li class="pledge"><svg class="person" width="11" height="12" viewBox="0 0 10 11"><circle cx="5" cy="3" r="2.8" fill="var(--teal)"/><path d="M0 11c0-3.5 2-5 5-5s5 1.5 5 5z" fill="var(--teal)"/></svg>I am in, $1 / Month<svg class="cart" width="14" height="13" viewBox="0 0 14 13"><path d="M0 1h2.5l2 7h7l1.5-5.5H4" fill="none" stroke="#555" stroke-width="1.6"/><circle cx="5.5" cy="11" r="1.3" fill="#555"/><circle cx="10.5" cy="11" r="1.3" fill="#555"/></svg></li>
      <li class="pledge"><svg class="person" width="11" height="12" viewBox="0 0 10 11"><circle cx="5" cy="3" r="2.8" fill="var(--teal)"/><path d="M0 11c0-3.5 2-5 5-5s5 1.5 5 5z" fill="var(--teal)"/></svg>Increased, $5 / Month<svg class="cart" width="14" height="13" viewBox="0 0 14 13"><path d="M0 1h2.5l2 7h7l1.5-5.5H4" fill="none" stroke="#555" stroke-width="1.6"/><circle cx="5.5" cy="11" r="1.3" fill="#555"/><circle cx="10.5" cy="11" r="1.3" fill="#555"/></svg></li>
      <li class="pledge"><svg class="person" width="11" height="12" viewBox="0 0 10 11"><circle cx="5" cy="3" r="2.8" fill="var(--teal)"/><path d="M0 11c0-3.5 2-5 5-5s5 1.5 5 5z" fill="var(--teal)"/></svg>Decent Help, $10 / Month<svg class="cart" width="14" height="13" viewBox="0 0 14 13"><path d="M0 1h2.5l2 7h7l1.5-5.5H4" fill="none" stroke="#555" stroke-width="1.6"/><circle cx="5.5" cy="11" r="1.3" fill="#555"/><circle cx="10.5" cy="11" r="1.3" fill="#555"/></svg></li>
      <li class="pledge"><svg class="person" width="11" height="12" viewBox="0 0 10 11"><circle cx="5" cy="3" r="2.8" fill="var(--teal)"/><path d="M0 11c0-3.5 2-5 5-5s5 1.5 5 5z" fill="var(--teal)"/></svg>Whole Kid, $35 / month<svg class="cart" width="14" height="13" viewBox="0 0 14 13"><path d="M0 1h2.5l2 7h7l1.5-5.5H4" fill="none" stroke="#555" stroke-width="1.6"/><circle cx="5.5" cy="11" r="1.3" fill="#555"/><circle cx="10.5" cy="11" r="1.3" fill="#555"/></svg></li>
      <li class="pledge"><svg class="person" width="11" height="12" viewBox="0 0 10 11"><circle cx="5" cy="3" r="2.8" fill="var(--teal)"/><path d="M0 11c0-3.5 2-5 5-5s5 1.5 5 5z" fill="var(--teal)"/></svg>My amount<span class="amount-input">Enter amount</span><svg class="cart" width="14" height="13" viewBox="0 0 14 13"><path d="M0 1h2.5l2 7h7l1.5-5.5H4" fill="none" stroke="#555" stroke-width="1.6"/><circle cx="5.5" cy="11" r="1.3" fill="#555"/><circle cx="10.5" cy="11" r="1.3" fill="#555"/></svg></li>
    </ul>
  </aside>
</div>
<footer class="site-footer">Copyright © 2016&nbsp; All Rights Reserved</footer>
</body>
</html>
```